Corvane Holdings , new business card design

investment firm with corporate clients . need double sided business card , vertical and horizontal options ,logo must be clear. prefer pantone colors only and sharp design. website also www.corvane.ae

Khalid Bin Tarrafi
Managing Director
Tel. +971 4 387 2940
Mobile +971 50 518 2403
khalid@corvane.ae
Q-Span Plaza, officw 18-B07, Warqa Gardens, Dubai

Contact Information for Business Card

Khalid Bin Tarrafi
Managing Director

Font styles to use
Serif

Colors

Designer to choose colors to be used in the design.

```html
<!DOCTYPE html>
<html lang="en">
<head>
<meta charset="utf-8">
<title>Corvane Holdings — Business Card</title>
<link href="https://fonts.googleapis.com/css2?family=Roboto:wght@300;400&family=Roboto+Condensed:wght@500;700&display=swap" rel="stylesheet">
<style>
  :root {
    --backdrop: #2b2b2d;
    --card-paper: #f1f1f1;
    --brand-blue: #47739a;
    --ink: #1a1a1a;
    --ink-soft: #4a4a4a;
    --rule: #9a9a9a;
    --white: #ffffff;
  }
  * { box-sizing: border-box; margin: 0; padding: 0; }
  html, body {
    width: 1200px; height: 960px; overflow: hidden;
    background: var(--backdrop);
    font-family: "Roboto", Arial, sans-serif;
  }
  .canvas { position: relative; width: 1200px; height: 960px; }

  .card {
    position: absolute; width: 600px; height: 343px;
  }
  .card--front { left: 152px; top: 125px; background: var(--card-paper); }
  .card--back  { left: 452px; top: 500px; background: var(--brand-blue); }

  .wordmark {
    position: absolute;
    font-family: "Roboto", Arial, sans-serif;
    font-weight: 300;
    text-transform: uppercase;
    white-space: nowrap;
  }
  .wordmark__main { display: block; font-size: 42px; letter-spacing: 0.28em; line-height: 1; }
  .wordmark__sub  { display: block; font-size: 14px; letter-spacing: 0.78em; line-height: 1; margin-top: 10px; }

  .card--front .wordmark { left: 38px; top: 60px; color: var(--ink); }
  .card--back .wordmark {
    left: 0; right: 0; top: 135px; text-align: center; color: var(--white);
  }
  .card--back .wordmark__main { padding-left: 0.28em; }
  .card--back .wordmark__sub  { padding-left: 0.78em; }

  .divider {
    position: absolute; left: 300px; top: 166px; width: 260px; height: 1px;
    background: var(--rule);
  }

  .holder { position: absolute; right: 40px; top: 172px; text-align: right; }
  .holder__name {
    font-family: "Roboto Condensed", "Arial Narrow", sans-serif;
    font-weight: 700; font-size: 21px; color: var(--brand-blue);
    text-transform: uppercase; line-height: 1.1;
  }
  .holder__title {
    font-family: "Roboto Condensed", "Arial Narrow", sans-serif;
    font-weight: 500; font-size: 15px; letter-spacing: 0.03em;
    color: var(--ink); text-transform: uppercase; margin-top: 4px;
  }

  .address {
    position: absolute; left: 38px; top: 185px;
    font-size: 14px; line-height: 19px; color: var(--ink-soft); font-style: normal;
  }

  .contact-list {
    position: absolute; left: 38px; top: 235px; list-style: none;
    font-size: 14px; line-height: 19px; color: var(--ink-soft);
  }
  .contact-list li { display: flex; align-items: center; gap: 7px; }
  .contact-list svg { width: 13px; height: 13px; fill: var(--brand-blue); flex: none; }

  .web-address {
    position: absolute; left: 0; right: 0; top: 290px; text-align: center;
    font-size: 14px; letter-spacing: 0.95em; padding-left: 0.95em;
    color: var(--white);
  }
</style>
</head>
<body>
<main class="canvas">

  <section class="card card--front" aria-label="Business card front">
    <div class="wordmark">
      <span class="wordmark__main">Corvane</span>
      <span class="wordmark__sub">Holdings</span>
    </div>

    <div class="divider"></div>

    <div class="holder">
      <p class="holder__name">Khalid Bin Tarrafi</p>
      <p class="holder__title">Managing Director</p>
    </div>

    <address class="address">
      Q-Span Plaza, officw 18-B07<br>
      Warqa Gardens, Dubai
    </address>

    <ul class="contact-list">
      <li>
        <svg viewBox="0 0 16 16" aria-hidden="true"><path d="M3.6 1.2l2.3 2.6c.4.4.4 1 0 1.4L4.8 6.4c.9 2 2.7 3.9 4.8 4.8l1.2-1.1c.4-.4 1-.4 1.4 0l2.6 2.3c.4.4.4 1 0 1.4l-1.4 1.3c-.5.5-1.3.6-2 .4C6.4 13.9 2.1 9.6.5 4.6.3 3.9.5 3.1 1 2.6L2.2 1.2c.4-.4 1-.4 1.4 0z"/></svg>
        <span>+971 4 387 2940</span>
      </li>
      <li>
        <svg viewBox="0 0 16 16" aria-hidden="true"><path d="M4.5 0h7A1.5 1.5 0 0 1 13 1.5v13a1.5 1.5 0 0 1-1.5 1.5h-7A1.5 1.5 0 0 1 3 14.5v-13A1.5 1.5 0 0 1 4.5 0zM4.5 2v10.5h7V2zm3.5 11.3a.9.9 0 1 0 0 1.8.9.9 0 0 0 0-1.8z"/></svg>
        <span>+971 50 518 2403</span>
      </li>
      <li>
        <svg viewBox="0 0 16 16" aria-hidden="true"><path d="M1 3h14v1.2L8 8.6 1 4.2zM1 5.6l7 4.4 7-4.4V13H1z"/></svg>
        <span>khalid@corvane.ae</span>
      </li>
      <li>
        <svg viewBox="0 0 16 16" aria-hidden="true"><path d="M8 0a8 8 0 1 0 0 16A8 8 0 0 0 8 0zm-1 2.2c-.4.9-.3 1.7-1.2 2.1-.9.4-1.9.2-2.3 1.1-.4.9.8 1.6 1.6 2 .8.4.6 1.6 1.1 2.3.5.7 1.3.6 1.3 1.7 0 1-.6 1.8-.2 2.5A6 6 0 0 1 7 2.2zm3.6.7a6 6 0 0 1 3.1 7.3c-.7-.4-1.2-1.2-2-1.3-.9-.1-1.5.6-2.3.2-.8-.4-.5-1.5 0-2.1.5-.6 1.5-.5 1.7-1.3.2-.8-.8-1.2-.8-2 0-.3.1-.6.3-.8z"/></svg>
        <span>www.corvane.ae</span>
      </li>
    </ul>
  </section>

  <section class="card card--back" aria-label="Business card back">
    <div class="wordmark">
      <span class="wordmark__main">Corvane</span>
      <span class="wordmark__sub">Holdings</span>
    </div>
    <p class="web-address">www.corvane.ae</p>
  </section>

</main>
</body>
</html>
```